TL - business card

Tallow Partners is an insurance brokerage firm, inovative, proactive, vigorous, which aims to become the leader of the insurance brokers in Anfrica. We should like to get some designs which should be avoided also in Gray / Metallic for the Administration and Orange / Blue for the Managers (ike in the picture sent). The Blue / Green logo is not the correct one, but the source of the file. Please adjust the color accordingly for the business cards. 1 / Orange / Blue 2 / Gray / Metallic We want something classic but which is transmitted strenght, inovation, modernity and most of all, rapidity. We want something start-up like, very punchy and catching eye remaining profesional at the same time. Name: Dorian Whitlock Function: Managing Director Address: N ° 17/18 Rua Veloso - R / C 2B Direita - Bairro Mutamba - Luanda Tel: (+244) 947 582 316 Email: dorian.whitlock@tallow-p.example Website: www.tallow-p. example We want classic in the front and creative, colorfull at the back. The cards will be printed in relief, with very high quality of paper.
Insurance Broker
Colors
Designer to choose colors to be used in the design.

```html
<!DOCTYPE html>
<html lang="en">
<head>
<meta charset="utf-8">
<title>Tallow Partners – Business Card</title>
<link rel="stylesheet" href="https://fonts.googleapis.com/css2?family=Lato:wght@400&family=Orbitron:wght@500;800&display=swap">
<style>
  :root {
    --backdrop: #e9e4dc;
    --kraft-light: #dcbb8e;
    --kraft-mid: #c49a68;
    --kraft-dark: #a87d4f;
    --ink: #111111;
    --card-shadow: rgba(0, 0, 0, 0.35);
  }
  html, body {
    margin: 0;
    padding: 0;
    width: 1200px;
    height: 900px;
    overflow: hidden;
    background: var(--backdrop);
  }
  .canvas {
    position: relative;
    width: 1200px;
    height: 900px;
  }
  .card {
    position: absolute;
    left: 330px;
    width: 557px;
    height: 343px;
    background: radial-gradient(ellipse at 25% 20%, var(--kraft-light) 0%, var(--kraft-mid) 55%, var(--kraft-dark) 100%);
    box-shadow: 3px 4px 6px var(--card-shadow);
    color: var(--ink);
    text-align: center;
  }
  .card--front { top: 90px; }
  .card--back { top: 470px; }

  .contact {
    position: absolute;
    left: 0;
    right: 0;
    top: 83px;
    font-family: "Lato", sans-serif;
    font-size: 15px;
    line-height: 20px;
    padding-left: 2px;
  }
  .contact__name {
    font-family: "Orbitron", sans-serif;
    font-weight: 500;
    font-size: 18px;
    letter-spacing: 0.5px;
    line-height: 22px;
    margin: 0;
  }
  .contact__role { margin: 0; }
  .contact__rule {
    width: 150px;
    height: 1px;
    background: var(--ink);
    margin: 7px auto 6px;
    border: 0;
  }
  .contact__line { margin: 0; }

  .brand {
    position: absolute;
    left: 0;
    right: 0;
    top: 210px;
    font-family: "Orbitron", sans-serif;
    font-weight: 800;
    font-size: 30px;
    letter-spacing: 0.5px;
    margin: 0;
    color: var(--ink);
  }
</style>
</head>
<body>
<div class="canvas">
  <section class="card card--front" aria-label="Business card front">
    <div class="contact">
      <p class="contact__name">DORIAN WHITLOCK</p>
      <p class="contact__role">Managing Director</p>
      <hr class="contact__rule">
      <p class="contact__line">(+244) 947 582 316</p>
      <p class="contact__line">dorian.whitlock@tallow-p.example</p>
      <hr class="contact__rule">
      <p class="contact__line">N ° 17/18 Rua Veloso - R / C</p>
      <p class="contact__line">2B Direita</p>
      <p class="contact__line">Bairro Mutamba - Luanda</p>
    </div>
  </section>

  <section class="card card--back" aria-label="Business card back">
    <p class="brand">TALLOW-PARTNERS</p>
  </section>
</div>
</body>
</html>
```